Request for Business Card Design

Hi. My name is Marlene, I am looking for a new business card design for my company, Quarrow Signal Instruments, LLC. I really like the design you did for Tarsel Venture and was hoping you could do something similar using our full logo and our mark. I am also open to any raised texture design using our mark. I have attached our full logo, which would need to be somewhere on the card, as well as the mark in both outline and full form, as well as our brand colors / guide. The card does not have to be white, as long as our logo and mark appear. I actually like darker colored business cards more, but am open to all options. If you are interested in working with me, please let me know. We would also take the business card design into letterhead design if you can do that.

```html
<!DOCTYPE html>
<html lang="en">
<head>
<meta charset="utf-8">
<title>Quarrow Signal Instruments – Business Card</title>
<link href="https://fonts.googleapis.com/css2?family=Barlow:wght@400;500;700&display=swap" rel="stylesheet">
<style>
  :root {
    --stage: #2b2d2f;
    --card-light: #2babca;
    --card-mid: #1f9cc2;
    --card-dark: #1683a9;
    --ink: #ffffff;
  }
  * { margin: 0; padding: 0; box-sizing: border-box; }
  html, body {
    width: 1200px; height: 1200px; overflow: hidden;
    background: var(--stage);
    font-family: "Barlow", Arial, sans-serif;
    color: var(--ink);
  }
  .sheet {
    position: relative; width: 1200px; height: 1200px;
    display: flex; flex-direction: column; align-items: center; justify-content: center; gap: 90px;
  }
  .card {
    position: relative; width: 700px; height: 400px;
    background: radial-gradient(ellipse at 50% 50%, var(--card-light) 0%, var(--card-mid) 55%, var(--card-dark) 100%);
    box-shadow: 0 14px 30px rgba(0,0,0,0.45);
    overflow: hidden;
  }
  /* brand lockup: plain circle + name */
  .brand { display: flex; align-items: center; gap: 16px; }
  .brand-dot { border-radius: 50%; background: var(--ink); flex: none; }
  .brand-name { font-weight: 700; letter-spacing: 0.06em; text-transform: uppercase; line-height: 1; }

  .card-front .brand { position: absolute; left: 50%; top: 50%; transform: translate(-50%, -50%); }
  .card-front .brand-dot { width: 64px; height: 64px; }
  .card-front .brand-name { font-size: 34px; }

  .card-back .brand { position: absolute; left: 48px; top: 48px; gap: 12px; }
  .card-back .brand-dot { width: 36px; height: 36px; }
  .card-back .brand-name { font-size: 19px; }

  .address {
    position: absolute; left: 48px; top: 236px;
    font-size: 17px; font-weight: 400; line-height: 1.35;
  }
  .person { position: absolute; left: 345px; top: 150px; }
  .person-name { font-size: 30px; font-weight: 700; line-height: 1.1; }
  .person-role { font-size: 19px; font-weight: 400; margin-top: 2px; }
  .divider {
    position: absolute; left: 330px; right: 0; top: 222px;
    height: 2px; background: var(--ink);
  }
  .contacts {
    position: absolute; left: 330px; top: 236px;
    list-style: none; font-size: 17px; line-height: 1.5;
  }
  .contacts li { display: flex; align-items: center; gap: 10px; }
  .contacts svg { width: 15px; height: 15px; flex: none; fill: var(--ink); }
</style>
</head>
<body>
<main class="sheet">
  <section class="card card-front" aria-label="Card front">
    <div class="brand">
      <span class="brand-dot"></span>
      <span class="brand-name">Quarrow Signal Instruments</span>
    </div>
  </section>

  <section class="card card-back" aria-label="Card back">
    <div class="brand">
      <span class="brand-dot"></span>
      <span class="brand-name">Quarrow Signal Instruments</span>
    </div>

    <p class="address">1180 Ledgerock Parkway.<br>Fernhill, CO 80977</p>

    <div class="person">
      <p class="person-name">Marlene</p>
      <p class="person-role">Founder &amp; Director</p>
    </div>
    <div class="divider"></div>

    <ul class="contacts">
      <li>
        <svg viewBox="0 0 16 16" aria-hidden="true"><path d="M3.6 1.2l2.2 2.6-1.2 1.8c.9 2 2.5 3.6 4.6 4.6l1.7-1.2 2.7 2.2-1.2 2.4C7.4 15.4.8 8.8 1.2 2.4z"/></svg>
        +001 555 014 2287
      </li>
      <li>
        <svg viewBox="0 0 16 16" aria-hidden="true"><path d="M4 1h8v4H4zM1 6h14v6h-3v3H4v-3H1zm4 4v3h6v-3z"/></svg>
        +001 555 014 2290
      </li>
      <li>
        <svg viewBox="0 0 16 16" aria-hidden="true"><path d="M1 3h14v10H1zm1.5 1.5L8 9l5.5-4.5z"/></svg>
        hello@quarrowsignal.com
      </li>
      <li>
        <svg viewBox="0 0 16 16" aria-hidden="true"><path d="M8 1a7 7 0 100 14A7 7 0 008 1zm0 1.5c.8 0 1.7 1.7 2 4.5H6c.3-2.8 1.2-4.5 2-4.5zM2.6 7h2c.1-1.6.4-3 .9-4A5.5 5.5 0 002.6 7zm8.8 0h2a5.5 5.5 0 00-2.9-4c.5 1 .8 2.4.9 4zM2.6 9a5.5 5.5 0 002.9 4c-.5-1-.8-2.4-.9-4zm3.4 0c.3 2.8 1.2 4.5 2 4.5s1.7-1.7 2-4.5zm5.4 0c-.1 1.6-.4 3-.9 4a5.5 5.5 0 002.9-4z"/></svg>
        www.quarrowsignal.com
      </li>
    </ul>
  </section>
</main>
</body>
</html>
```